KTR Design Business Card

I need to develop a business card for my real estate design and investment company. Something clean, classic and professional with a modern vibe.

Industry/Entity Type

Real Estate

Font styles to use
Serif
Sans Serif

```html
<!DOCTYPE html>
<html lang="en">
<head>
<meta charset="utf-8">
<title>KTR Design Business Card</title>
<link rel="stylesheet" href="https://fonts.googleapis.com/css2?family=Josefin+Sans:ital,wght@0,300;0,400;0,600;1,300&display=swap">
<style>
  :root {
    --page: #e9e9e7;
    --card: #ffffff;
    --band: #3a3a3a;
    --band-edge: #b9b9b9;
    --ink: #2b2b2b;
    --ink-soft: #555555;
    --on-band: #f2f2f2;
  }
  * { box-sizing: border-box; margin: 0; padding: 0; }
  html, body { width: 1200px; height: 901px; overflow: hidden; }
  body {
    background: var(--page);
    font-family: "Josefin Sans", sans-serif;
    color: var(--ink);
    position: relative;
  }
  .card {
    position: absolute;
    top: 300px;
    width: 525px;
    height: 300px;
    background: var(--card);
    border-radius: 24px;
    overflow: hidden;
    box-shadow: 0 6px 18px rgba(0,0,0,0.12);
  }
  .card--front { left: 50px; }
  .card--back { left: 625px; }
  .card__band { position: absolute; inset: 0; width: 100%; height: 100%; }
  .card__website {
    position: absolute;
    left: 0; right: 0; bottom: 20px;
    text-align: center;
    font-size: 13px;
    letter-spacing: 0.18em;
    color: var(--on-band);
    font-weight: 400;
  }
  .brand {
    position: absolute;
    left: 0; right: 0;
    text-align: center;
  }
  .brand__name {
    font-weight: 300;
    color: var(--ink);
    letter-spacing: 0.12em;
    text-transform: uppercase;
    white-space: nowrap;
    line-height: 1;
  }
  .brand__tagline {
    font-style: italic;
    font-weight: 300;
    color: var(--ink-soft);
    letter-spacing: 0.04em;
    white-space: nowrap;
  }
  .card--front .brand { top: 38px; }
  .card--front .brand__name { font-size: 32px; }
  .card--front .brand__tagline { font-size: 12px; margin-top: 6px; }
  .card--back .brand { top: 96px; }
  .card--back .brand__name { font-size: 44px; }
  .card--back .brand__tagline { font-size: 15px; margin-top: 10px; }
  .details {
    position: absolute;
    top: 108px; left: 30px; right: 30px;
    display: flex;
    justify-content: center;
    gap: 18px;
  }
  .details__person {
    text-align: right;
    text-transform: uppercase;
    letter-spacing: 0.1em;
  }
  .person__name { font-weight: 600; font-size: 14px; }
  .person__title { font-size: 10px; color: var(--ink-soft); margin-top: 5px; }
  .person__address { font-size: 10px; color: var(--ink-soft); margin-top: 14px; line-height: 1.6; }
  .details__divider { width: 1px; background: var(--ink); }
  .details__contacts { list-style: none; font-size: 11px; letter-spacing: 0.08em; text-transform: uppercase; }
  .contact { display: flex; align-items: center; gap: 8px; line-height: 17px; white-space: nowrap; }
  .contact__icon { width: 10px; height: 10px; flex: none; }
</style>
</head>
<body>
  <section class="card card--front">
    <svg class="card__band" viewBox="0 0 525 300" preserveAspectRatio="none" aria-hidden="true">
      <path d="M0 218 Q250 262 525 236 L525 300 L0 300 Z" fill="var(--band-edge)"/>
      <path d="M0 226 Q250 270 525 244 L525 300 L0 300 Z" fill="var(--band)"/>
    </svg>
    <div class="brand">
      <p class="brand__name">KTR Design</p>
      <p class="brand__tagline">Design and Productions</p>
    </div>
    <div class="details">
      <div class="details__person">
        <p class="person__name">Daniel Reyes</p>
        <p class="person__title">Owner / C.E.O</p>
        <p class="person__address">Suite # 410, Crest Bldg.<br>NY 10458</p>
      </div>
      <div class="details__divider"></div>
      <ul class="details__contacts">
        <li class="contact"><svg class="contact__icon" viewBox="0 0 10 10"><circle cx="5" cy="5" r="5" fill="var(--ink)"/><path d="M3.3 2.6 L4.2 3.6 L3.8 4.3 Q4.6 5.6 5.7 6.2 L6.4 5.8 L7.4 6.7 L6.8 7.5 Q4.4 7.1 2.6 3.3 Z" fill="#fff"/></svg>212-555-0148</li>
        <li class="contact"><svg class="contact__icon" viewBox="0 0 10 10"><circle cx="5" cy="5" r="5" fill="var(--ink)"/><path d="M3.3 2.6 L4.2 3.6 L3.8 4.3 Q4.6 5.6 5.7 6.2 L6.4 5.8 L7.4 6.7 L6.8 7.5 Q4.4 7.1 2.6 3.3 Z" fill="#fff"/></svg>212-555-0173</li>
        <li class="contact"><svg class="contact__icon" viewBox="0 0 10 10"><circle cx="5" cy="5" r="5" fill="var(--ink)"/><rect x="2.8" y="3.2" width="4.4" height="3.6" fill="#fff"/></svg>212-555-0196</li>
        <li class="contact"><svg class="contact__icon" viewBox="0 0 10 10"><circle cx="5" cy="5" r="5" fill="var(--ink)"/><rect x="2.6" y="3.2" width="4.8" height="3.6" fill="#fff"/><path d="M2.6 3.2 L5 5.2 L7.4 3.2" stroke="var(--ink)" stroke-width="0.6" fill="none"/></svg>daniel@ktrdesign.example</li>
        <li class="contact"><svg class="contact__icon" viewBox="0 0 10 10"><circle cx="5" cy="5" r="5" fill="var(--ink)"/><circle cx="5" cy="5" r="2.4" fill="none" stroke="#fff" stroke-width="0.8"/></svg>www.ktrdesign.example</li>
      </ul>
    </div>
    <p class="card__website">www.example.com</p>
  </section>

  <section class="card card--back">
    <svg class="card__band" viewBox="0 0 525 300" preserveAspectRatio="none" aria-hidden="true">
      <path d="M0 218 Q250 262 525 236 L525 300 L0 300 Z" fill="var(--band-edge)"/>
      <path d="M0 226 Q250 270 525 244 L525 300 L0 300 Z" fill="var(--band)"/>
    </svg>
    <div class="brand">
      <p class="brand__name">KTR Design</p>
      <p class="brand__tagline">Design and Productions</p>
    </div>
    <p class="card__website">www.example.com</p>
  </section>
</body>
</html>
```